Redesign and move to Wordpress for corvandel.com

Our website needs a redesign and at the same time we are moving it to Wordpress. Please help us with a new digital professional look and feel.

We are an Australian Software Engineering company specialising in advanced software development using in A.I., PLatform Engineering, Integration and Cloud. See the current corvandel.com for more information about us.

```html
<!DOCTYPE html>
<html lang="en">
<head>
<meta charset="utf-8">
<title>corvandel — Reliable Smart Software Engineering</title>
<link rel="stylesheet" href="https://fonts.googleapis.com/css2?family=Tomorrow:wght@300;400;500&family=Poppins:wght@300;400;500&display=swap">
<style>
:root{
  --bg:#030b1f;
  --panel:#061230;
  --line:#12244a;
  --cyan:#2ed3c6;
  --cyan-soft:#37b8e8;
  --blue:#1e5fa8;
  --white:#ffffff;
  --muted:#b8c3d6;
  --navy:#0b2a5a;
  --cta:#2fd3c3;
}
*{box-sizing:border-box;margin:0;padding:0}
h1,h2,h3{font-weight:400}
html,body{width:1200px;height:3125px;overflow:hidden;background:var(--bg)}
body{font-family:"Poppins",sans-serif;color:var(--white)}
.page{position:relative;width:1200px;height:3125px;overflow:hidden;background:linear-gradient(180deg,#040c22 0%,var(--bg) 40%,#030a1c 100%)}
.abs{position:absolute}
.display{font-family:"Tomorrow",sans-serif;font-weight:400}

/* header */
.brand{left:112px;top:20px;display:flex;align-items:center;gap:10px}
.brand-mark{width:30px;height:30px;border:3px solid var(--white)}
.brand-name{font-family:"Tomorrow",sans-serif;font-size:27px;font-weight:400;letter-spacing:1px}
.nav{top:28px;font-size:11px;color:var(--white)}
.nav.active{color:var(--cyan)}
.caret{display:inline-block;margin-left:4px;color:var(--cyan)}
.search{left:948px;top:29px}
.btn-outline{left:982px;top:19px;width:104px;height:33px;border:1px solid var(--cyan);display:flex;align-items:center;justify-content:center;gap:12px;font-size:11px}
.sq{display:inline-block;width:8px;height:8px;border:1.5px solid currentColor}
.sq.fill{background:currentColor}

/* hero */
.hero-eyebrow{left:0;width:1200px;top:117px;text-align:center;color:var(--cyan);font-size:16px;font-weight:500}
.hero-title{left:0;width:1200px;top:136px;text-align:center;font-size:44px;letter-spacing:1px}
.hero-photo{left:0;top:188px;width:1200px;height:480px;background:
  radial-gradient(ellipse 140px 190px at 37% 38%,rgba(196,150,118,.75) 0%,rgba(150,110,90,.35) 55%,transparent 100%),
  radial-gradient(ellipse 200px 110px at 46% 78%,rgba(214,206,196,.55) 0%,transparent 100%),
  radial-gradient(ellipse 170px 120px at 64% 47%,rgba(40,120,170,.85) 0%,rgba(20,70,120,.45) 60%,transparent 100%),
  radial-gradient(ellipse 140px 140px at 85% 42%,rgba(40,110,170,.7) 0%,transparent 100%),
  radial-gradient(ellipse 60px 50px at 93% 50%,rgba(245,232,200,.85) 0%,transparent 100%),
  radial-gradient(ellipse 220px 240px at 10% 45%,rgba(40,100,170,.55) 0%,transparent 100%),
  radial-gradient(ellipse 120px 60px at 70% 90%,rgba(200,40,60,.35) 0%,transparent 100%),
  linear-gradient(180deg,#0b1c40 0%,#10284f 45%,#0a1a3a 82%,var(--bg) 100%)}

/* section titles */
.sec-title{font-size:31px;text-align:center}

/* insights */
.card{border:1px solid var(--line);background:linear-gradient(180deg,#071535,#050f28)}
.card-title{font-family:"Tomorrow",sans-serif;font-weight:400;font-size:17px;text-align:center;width:100%;position:absolute;top:31px}
.card-sub{position:absolute;top:54px;left:20px;right:20px;text-align:center;color:var(--cyan-soft);font-size:11px;line-height:13px}
.card-text{position:absolute;top:91px;left:40px;right:40px;text-align:center;color:var(--muted);font-size:10.5px;line-height:15px}
.card-img{position:absolute;top:171px;left:19px;right:19px;height:161px}
.arrow-dot{width:16px;height:16px;border-radius:50%;background:var(--cyan);display:flex;align-items:center;justify-content:center}
.btn-solid{background:var(--cta);color:var(--navy);display:flex;align-items:center;justify-content:center;gap:18px;font-size:12px}

/* partners & customers */
.logo-box{border:1px solid var(--line);background:linear-gradient(160deg,#0a1c44,#050f28);display:flex;align-items:center;justify-content:center;gap:7px;font-family:"Tomorrow",sans-serif;font-weight:500;color:var(--white)}
.logo-dot{width:12px;height:12px;border-radius:50%;background:var(--white)}

/* services */
.svc{border:1px solid var(--line);background:linear-gradient(180deg,#061333,#040c24)}
.svc.featured{background:linear-gradient(160deg,#0c3a52,#0a2540);border-color:#123a5a}
.svc-icon{position:absolute;left:50%;top:31px;width:66px;height:66px;margin-left:-33px;border-radius:50%;background:#0d2250;display:flex;align-items:center;justify-content:center}
.svc.featured .svc-icon{background:var(--cyan)}
.svc-title{position:absolute;top:110px;width:100%;text-align:center;font-family:"Tomorrow",sans-serif;font-weight:400;font-size:17px;line-height:20px}
.svc-text{position:absolute;left:40px;right:40px;text-align:center;color:var(--muted);font-size:10.5px;line-height:15px}
.svc-arrow{position:absolute;left:50%;margin-left:-8px;color:var(--cyan)}
.svc-corner{position:absolute;right:-1px;bottom:-1px;width:14px;height:14px;border:1px solid var(--line);background:var(--bg)}
.svc.featured .svc-corner{background:var(--cyan);border-color:var(--cyan)}

/* about */
.frame-blue{background:var(--blue)}
.frame-teal{background:linear-gradient(180deg,#2bb7b4,#1a5a78)}
.stat-inner{background:#04102a;text-align:center}
.about-photo{display:flex;flex-direction:column;align-items:center;justify-content:flex-end;text-align:center}
.about-title{left:690px;top:1968px;font-size:32px}
.about-copy{left:690px;top:2022px;width:380px;display:flex;flex-direction:column;gap:15px}
.about-copy p{color:var(--muted);font-size:10px;line-height:15.6px}
.read-more{left:690px;top:2269px;width:113px;height:33px;border:1px solid var(--cyan-soft);display:flex;align-items:center;justify-content:center;gap:20px;font-size:11px;font-weight:500}
.grid-floor{left:0;top:2305px;width:1200px;height:103px;background:
  repeating-linear-gradient(90deg,rgba(46,211,198,.10) 0 1px,transparent 1px 40px),
  linear-gradient(180deg,transparent,rgba(20,80,140,.35))}

/* cta */
.cta{left:0;top:2408px;width:1200px;height:377px;background:var(--cta)}
.cta-deco{width:90px;height:90px;border:4px solid rgba(255,255,255,.35)}
.cta-title{left:0;width:1200px;top:2454px;text-align:center;font-size:32px;color:#f2fffe}
.field{border:1px solid var(--navy);font-size:12px;color:var(--navy);padding:11px 17px;height:35px}
.field.msg{height:64px}
.submit{left:531px;top:2685px;width:135px;height:35px;background:var(--navy);display:flex;align-items:center;justify-content:center;gap:38px;font-size:11px;border:0;color:#fff;font-family:"Poppins",sans-serif}

/* footer */
.foot-text{font-size:10px;line-height:15px;color:var(--white)}
.foot-head{font-family:"Tomorrow",sans-serif;font-weight:400;font-size:17px}
.foot-link{font-size:10px;color:var(--white)}
.icon-circle{width:14px;height:14px;border:1px solid var(--white);border-radius:50%;display:inline-flex;align-items:center;justify-content:center;vertical-align:middle;margin-right:7px}
.watermark{left:0;width:1200px;top:2960px;text-align:center;font-family:"Tomorrow",sans-serif;font-size:140px;color:rgba(255,255,255,.04);letter-spacing:4px}
</style>
</head>
<body>
<div class="page">

  <!-- header -->
  <div class="abs brand"><span class="brand-mark"></span><span class="brand-name">corvandel</span></div>
  <div class="abs nav active" style="left:471px">Home</div>
  <div class="abs nav" style="left:539px">About Us</div>
  <div class="abs nav" style="left:625px">Services<span class="caret">⌄</span></div>
  <div class="abs nav" style="left:707px">Blog</div>
  <svg class="abs search" width="12" height="12" viewBox="0 0 12 12"><circle cx="5" cy="5" r="3.8" fill="none" stroke="#fff" stroke-width="1.3"/><line x1="8" y1="8" x2="11" y2="11" stroke="#fff" stroke-width="1.3"/></svg>
  <div class="abs btn-outline">Contact Us <span class="sq"></span></div>

  <!-- hero -->
  <div class="abs hero-photo" role="img" aria-label="Developer wearing headphones working at two monitors showing code in a dim blue-lit office with a desk lamp"></div>
  <div class="abs hero-eyebrow">Welcome to corvandel</div>
  <h1 class="abs hero-title display">Reliable Smart Software Engineering</h1>

  <!-- insights -->
  <h2 class="abs sec-title display" style="left:0;width:1200px;top:685px">Insights</h2>
  <div class="abs arrow-dot" style="left:77px;top:927px"><svg width="8" height="8" viewBox="0 0 8 8"><path d="M5 1 L2 4 L5 7" fill="none" stroke="#03112a" stroke-width="1.6"/></svg></div>
  <div class="abs arrow-dot" style="left:1107px;top:927px"><svg width="8" height="8" viewBox="0 0 8 8"><path d="M3 1 L6 4 L3 7" fill="none" stroke="#03112a" stroke-width="1.6"/></svg></div>

  <article class="abs card" style="left:113px;top:746px;width:317px;height:352px">
    <h3 class="card-title">Ai in Software Engineering</h3>
    <p class="card-sub">10 unexpected ways to use<br>PairCoder Assist</p>
    <p class="card-text">(CodeHarbor Blog) PairCoder Assist is widely known for its code generation feature. Learn how the AI assistant's abilities can extend beyond just code generation.</p>
    <div class="card-img" role="img" aria-label="Grey computer towers linked by black cables on a white surface" style="background:linear-gradient(135deg,#e8e8e8,#9a9a9a 50%,#dedede)"></div>
  </article>
  <article class="abs card" style="left:449px;top:746px;width:304px;height:352px">
    <h3 class="card-title">Industry Research</h3>
    <p class="card-sub">PROMA: A general-purpose framework<br>for prompt optimization</p>
    <p class="card-text">(Quadrant Research) Large language models (LLMs) have revolutionized various tasks, but prompt engineering remains a challenge.</p>
    <div class="card-img" role="img" aria-label="Glowing futuristic screen with golden data lights" style="background:radial-gradient(circle at 45% 50%,#d2a54a 0%,#3d5a6a 40%,#18324a 80%)"></div>
  </article>
  <article class="abs card" style="left:784px;top:746px;width:304px;height:352px">
    <h3 class="card-title">Business Insights</h3>
    <p class="card-sub">How Storytelling Helps Data-driven<br>Teams Succeed</p>
    <p class="card-text">(Halden School of Management) Winning leaders know that data alone isn't enough. It's the art of storytelling that drives sustained performance.</p>
    <div class="card-img" role="img" aria-label="Team meeting around a table with a presenter at a whiteboard diagram" style="background:linear-gradient(160deg,#d6d8dc,#8a7a66 55%,#4a3a2c)"></div>
  </article>

  <a class="abs btn-solid" style="left:502px;top:1123px;width:197px;height:37px">View All News &amp; Articles <span class="sq fill"></span></a>

  <!-- partners & customers -->
  <h2 class="abs sec-title display" style="left:142px;width:300px;top:1206px">Our Partners</h2>
  <h2 class="abs sec-title display" style="left:745px;width:300px;top:1209px">Our Customers</h2>

  <div class="abs logo-box" style="left:113px;top:1269px;width:178px;height:79px;font-size:18px"><span class="logo-dot"></span>Arpeggio</div>
  <div class="abs logo-box" style="left:305px;top:1269px;width:178px;height:110px;font-size:20px">Quadrant</div>
  <div class="abs logo-box" style="left:113px;top:1361px;width:178px;height:112px;font-size:20px">CodeHarbor</div>
  <div class="abs logo-box" style="left:305px;top:1393px;width:178px;height:80px;font-size:24px">Kestrel</div>

  <div class="abs" style="left:548px;top:1320px;width:110px;height:110px;border:5px solid var(--blue)"></div>

  <div class="abs logo-box" style="left:713px;top:1270px;width:117px;height:96px;font-size:12px;line-height:13px;text-align:center">Harbourside<br>Mutual</div>
  <div class="abs logo-box" style="left:842px;top:1270px;width:116px;height:96px;font-size:17px">Solaris Super</div>
  <div class="abs logo-box" style="left:971px;top:1270px;width:115px;height:96px;font-size:14px;text-align:center;line-height:16px">Meridian<br>Bank</div>
  <div class="abs logo-box" style="left:713px;top:1378px;width:117px;height:96px;font-size:20px">Valeway</div>
  <div class="abs logo-box" style="left:842px;top:1378px;width:116px;height:96px;font-size:20px">Northmark</div>
  <div class="abs logo-box" style="left:971px;top:1378px;width:115px;height:96px;font-size:9px;letter-spacing:1px">RIDGELINE GROUP</div>

  <!-- services -->
  <h2 class="abs sec-title display" style="left:0;width:1200px;top:1523px">Our Services</h2>

  <article class="abs svc" style="left:110px;top:1585px;width:309px;height:248px">
    <div class="svc-icon"><svg width="38" height="38" viewBox="0 0 38 38" fill="none" stroke="#2ed3c6" stroke-width="1.6"><circle cx="14" cy="14" r="6"/><circle cx="14" cy="14" r="2"/><circle cx="25" cy="25" r="6"/><circle cx="25" cy="25" r="2"/><path d="M14 5v3M14 20v3M5 14h3M20 14h3M25 16v3M25 31v3M16 25h3M31 25h3"/></svg></div>
    <h3 class="svc-title">Enterprise Systems Integration</h3>
    <p class="svc-text" style="top:141px">Automate your business processes internally or externally to improve data quality and process efficiency.</p>
    <span class="svc-arrow" style="top:198px">→</span>
    <span class="svc-corner"></span>
  </article>
  <article class="abs svc" style="left:444px;top:1585px;width:307px;height:248px">
    <div class="svc-icon"><svg width="38" height="38" viewBox="0 0 38 38" fill="none" stroke="#2ed3c6" stroke-width="1.6"><ellipse cx="16" cy="9" rx="9" ry="3.5"/><path d="M7 9v18c0 2 4 3.5 9 3.5M25 9v9M7 15c0 2 4 3.5 9 3.5s9-1.5 9-3.5M7 21c0 2 4 3.5 9 3.5"/><circle cx="27" cy="27" r="6" fill="#2ed3c6"/><path d="M27 24v3l2 2" stroke="#0d2250"/></svg></div>
    <h3 class="svc-title">Real-time Data Analytics</h3>
    <p class="svc-text" style="top:141px">Being able to react to changing business conditions in a precise intelligent way is becoming increasingly important.</p>
    <span class="svc-arrow" style="top:198px">→</span>
    <span class="svc-corner"></span>
  </article>
  <article class="abs svc featured" style="left:779px;top:1585px;width:307px;height:248px">
    <div class="svc-icon"><svg width="40" height="40" viewBox="0 0 40 40" fill="none" stroke="#ffffff" stroke-width="1.6"><circle cx="20" cy="20" r="14"/><circle cx="20" cy="20" r="7"/><circle cx="20" cy="20" r="2.5"/><path d="M20 3v5M20 32v5M3 20h5M32 20h5M8 8l3.5 3.5M28.5 28.5L32 32M8 32l3.5-3.5M28.5 11.5L32 8"/></svg></div>
    <h3 class="svc-title">Custom Development of<br>Intelligent Business Applications</h3>
    <p class="svc-text" style="top:161px">Our expertise in platform engineering, iPaaS, building distributed systems &amp; enterprise systems integration.</p>
    <span class="svc-arrow" style="top:210px">→</span>
    <span class="svc-corner"></span>
  </article>

  <a class="abs btn-solid" style="left:522px;top:1868px;width:155px;height:36px">View All Services <span class="sq fill"></span></a>

  <!-- about -->
  <div class="abs frame-blue" style="left:113px;top:1967px;width:192px;height:114px"></div>
  <div class="abs stat-inner" style="left:131px;top:1984px;width:157px;height:80px">
    <div style="font-size:12px;margin-top:12px">Company size:</div>
    <div class="display" style="font-size:48px;line-height:46px">500+</div>
  </div>

  <div class="abs frame-teal" style="left:113px;top:2109px;width:192px;height:221px"></div>
  <div class="abs about-photo" role="img" aria-label="Colleagues working on laptops in a meeting room" style="left:129px;top:2123px;width:159px;height:192px;background:linear-gradient(180deg,#5a6a80,#2a3448 55%,#0c1630)">
    <div class="display" style="font-size:34px;line-height:36px">2013</div>
    <div style="font-size:13px;margin-bottom:18px">Founded year</div>
  </div>

  <div class="abs frame-blue" style="left:336px;top:1967px;width:192px;height:222px"></div>
  <div class="abs about-photo" role="img" aria-label="Glowing medical cross held above an open hand" style="left:354px;top:1982px;width:157px;height:190px;background:radial-gradient(circle at 50% 40%,#8fe3f2 0%,#2a6fa8 35%,#0b1d44 80%)">
    <div class="display" style="font-size:15px;line-height:19px;margin-bottom:14px">Health &amp; Finance<br>Enterprise</div>
  </div>

  <div class="abs frame-teal" style="left:336px;top:2215px;width:192px;height:115px"></div>
  <div class="abs about-photo" role="img" aria-label="Hand reaching toward a glowing digital network display" style="left:354px;top:2232px;width:157px;height:83px;background:linear-gradient(135deg,#1a4f9a,#2a7fc8 50%,#0c1e48)">
    <div class="display" style="font-size:15px;margin-bottom:26px">Tech Geography</div>
  </div>

  <h2 class="abs about-title display">About Us corvandel</h2>
  <div class="abs about-copy">
    <p>Since our inception in 2013, we have been on a mission to make complex custom enterprise integration accessible to any organization, regardless of industry, size, or location.</p>
    <p>Our journey began with a focus on Integration Architecture, quickly moving into delivering bespoke systems integration using Quadrant technologies like FlowBridge, NovaNet, DataVault Server, and ServiceWire. Our commitment to excellence quickly earned us recognition, &amp; in 2014, we became a proud Quadrant Gold Partner, achieving this accolade with the creation of our first 100% native Stratus cloud solution. We have upheld this esteemed partnership ever since.</p>
    <p>By 2017, we had implemented one of the first large-scale Quadrant Stratus iPaaS solutions in Australia, pioneering the use of new Stratus integration products in conjunction with the Quadrant Product Team.</p>
  </div>
  <a class="abs read-more">Read More <span class="sq"></span></a>

  <div class="abs grid-floor"></div>

  <!-- contact cta -->
  <section class="abs cta"></section>
  <div class="abs cta-deco" style="left:-8px;top:2408px"></div>
  <div class="abs cta-deco" style="left:1112px;top:2693px"></div>
  <h2 class="abs cta-title display">Tomorrow, Delivered Today</h2>
  <div class="abs field" style="left:314px;top:2515px;width:278px">First Name*</div>
  <div class="abs field" style="left:604px;top:2515px;width:278px">Last Name*</div>
  <div class="abs field" style="left:314px;top:2563px;width:278px">Email*</div>
  <div class="abs field" style="left:604px;top:2563px;width:278px">Mobile Phone Number*</div>
  <div class="abs field msg" style="left:314px;top:2609px;width:568px">Message</div>
  <button class="abs submit">Submit <span class="sq fill"></span></button>

  <!-- footer -->
  <div class="abs watermark">corvandel</div>

  <div class="abs brand" style="top:2826px"><span class="brand-mark"></span><span class="brand-name">corvandel</span></div>
  <p class="abs foot-text" style="left:112px;top:2884px;width:260px">We have been on a mission to make complex custom enterprise integration accessible to any organisation, regardless of industry, size, or location</p>
  <p class="abs foot-text" style="left:112px;top:2939px">© 2025 All Rights Reserved By Corvandel</p>

  <h3 class="abs foot-head" style="left:427px;top:2827px">Contact Us</h3>
  <div class="abs foot-link" style="left:427px;top:2864px"><span class="icon-circle"><svg width="7" height="8" viewBox="0 0 7 8"><path d="M3.5 7.5C1 5 .8 3.8.8 3a2.7 2.7 0 015.4 0c0 .8-.2 2-2.7 4.5z" fill="none" stroke="#fff"/></svg></span>Suite 210, 48 Harbour Lane Melbourne, VIC, 3000</div>
  <div class="abs foot-link" style="left:427px;top:2889px"><span class="icon-circle"><svg width="8" height="8" viewBox="0 0 8 8"><path d="M1 1.5c0 3 2.5 5.5 5.5 5.5l.5-1.5-1.5-1-1 .8C3.5 4.8 3.2 4.5 2.7 3.5l.8-1L2.5 1z" fill="#fff"/></svg></span>1800 555 019</div>
  <div class="abs foot-link" style="left:427px;top:2914px;color:var(--cyan)"><span class="icon-circle"><svg width="8" height="6" viewBox="0 0 8 6"><rect x=".5" y=".5" width="7" height="5" fill="none" stroke="#fff"/><path d="M.5.5L4 3.5 7.5.5" fill="none" stroke="#fff"/></svg></span>info@corvandel.com</div>

  <h3 class="abs foot-head" style="left:751px;top:2827px">Quick Links</h3>
  <div class="abs foot-link" style="left:752px;top:2860px">Home</div>
  <div class="abs foot-link" style="left:752px;top:2880px">About</div>
  <div class="abs foot-link" style="left:752px;top:2900px">Services</div>
  <div class="abs foot-link" style="left:752px;top:2920px">Blog</div>
  <div class="abs foot-link" style="left:752px;top:2940px">Contact Us</div>

  <h3 class="abs foot-head" style="left:933px;top:2827px">Follow Us</h3>
  <div class="abs foot-link" style="left:933px;top:2864px"><span class="icon-circle"></span>Socialsphere</div>
  <div class="abs foot-link" style="left:933px;top:2889px"><span class="icon-circle"></span>Workline</div>
  <div class="abs foot-link" style="left:933px;top:2914px"><span class="icon-circle"></span>Chirpnet</div>

</div>
</body>
</html>
```